Web Design job - Condo Debts Collection Business needs a Web Design

I need a site for a client, who works with condo debts collection, and ensure all revenues provided by condo fees will be always available to the building manager of condo on a specific date, regardless of defaults.
I have the visual identity (logo, slogan and colors) of the company, and some requirements on layout (kind of slider, menu options, phone number on a noble position, etc) - maybe I can do a sketch, but I like the idea of give some freedom to designer.

*** PLEASE, we have no interest in templates. We want something new***

Target Market(s)

I have two targets for this design: - Condominium's building manager. This target is looking for a solution to overdue debts on it's condo. - Residents on condominiums. This target wants to live in a better place, where their neighbors pay their condominium fees on time.

Number of Pages Required

1 page

Requirements
Must have
• - Slider with title, some short text related, a nice image (I prefer happy and/or peaceful family, people doing business, happy friends, and so on).
• - I have a special attention to menu. I'm looking for one I can have a nice effect, more elegant, charming, kind of innovative.
• - Phone number on the top (or clearly visible).
• - Member log in area or icon on the top (or clearly visible).
• - News/articles area.
• - Modern fonts, with good quality, sans-serif on areas where reading is more intensive (prefer Google web-fonts).
• - Colors specified on attached files.
Nice to have
• - Clear background color, cause it's better to read larger texts (like articles). Dark backgrounds makes reading difficult.
• - A site with effects (like shadows, lines, curves, gradients, lights) is usually pretty.
• - I pay attention on beautiful footers.
Should not have
• - Images with a lot of money (I don't sell richness, I sell tranquility, peace, harmony, safety).
• - Poor menu.

```html
<!DOCTYPE html>
<html lang="en">
<head>
<meta charset="utf-8">
<title>Condara – Condominium Fee Collection</title>
<link rel="stylesheet" href="https://fonts.googleapis.com/css2?family=Open+Sans:wght@400;600;700&family=Lato:wght@400;700&display=swap">
<style>
  :root{
    --gold:#e9a81f;
    --gold-light:#f2c23c;
    --ink:#2e2e2e;
    --text:#555;
    --muted:#7a7a7a;
    --black:#0b0b0b;
    --white:#fff;
    --cream:#fffdf8;
    --line:#e6b04a;
  }
  *{box-sizing:border-box;margin:0;padding:0}
  html,body{width:1200px;height:2687px;overflow:hidden}
  body{position:relative;background:var(--white);font-family:"Lato",sans-serif;color:var(--text)}
  a{color:inherit;text-decoration:none}
  .abs{position:absolute}

  /* top bar */
  .topbar{left:0;top:0;width:1200px;height:43px;background:var(--black);color:var(--white)}
  .topbar .cta{left:100px;top:7px;width:100px;height:29px;background:#e9e9e9;color:#222;font:700 11px "Open Sans",sans-serif;display:flex;align-items:center;justify-content:center}
  .topbar .cta-note{left:213px;top:12px;font:600 14px "Open Sans",sans-serif}
  .topbar .phone{left:810px;top:11px;font:400 16px "Open Sans",sans-serif;display:flex;align-items:center;gap:8px}
  .topbar .login{left:982px;top:0;width:118px;height:43px;background:var(--gold);font:600 15px "Open Sans",sans-serif;display:flex;align-items:center;justify-content:center;gap:7px}

  /* nav */
  .nav{left:0;top:43px;width:1200px;height:81px;background:var(--white)}
  .brand{left:100px;top:18px;display:flex;align-items:center;gap:12px;font:700 40px "Open Sans",sans-serif;color:var(--ink);letter-spacing:-1px}
  .brand .mark{width:34px;height:34px;background:var(--gold)}
  .menu{right:99px;top:31px;display:flex;gap:29px;font:600 15px "Open Sans",sans-serif;color:var(--ink);align-items:center}

  /* hero */
  .hero{left:0;top:124px;width:1200px;height:539px;background:linear-gradient(90deg,#8aa6b8 0%,#c7d9e3 30%,#e4eef0 55%,#f3f0d6 80%,#f1ebc4 100%)}
  .hero-title{right:100px;top:148px;font:700 68px "Open Sans",sans-serif;color:#1e1e1e}
  .hero-text{right:100px;top:239px;width:460px;text-align:right;font:700 19px/27px "Open Sans",sans-serif;color:#222}
  .btn-gold{background:var(--gold);color:var(--white);font:600 14px "Open Sans",sans-serif;display:flex;align-items:center;justify-content:center}
  .hero .btn-gold{left:962px;top:324px;width:138px;height:46px}
  .dots{left:574px;top:488px;display:flex;gap:4px}
  .dots span{width:10px;height:10px;border-radius:50%;background:var(--white)}
  .dots span.on{background:var(--gold)}

  /* about */
  .section-title{font:600 40px/46px "Open Sans",sans-serif;color:var(--ink)}
  .section-title .accent{color:var(--gold)}
  .about-title{left:181px;top:782px}
  .about-copy{left:181px;top:897px;width:360px;font:400 12.5px/26px "Lato",sans-serif;color:var(--text)}
  .about-copy p+p{margin-top:13px}
  .btn-outline{left:181px;top:1141px;width:148px;height:43px;border:2px solid var(--gold);color:var(--gold);font:700 12px "Lato",sans-serif;display:flex;align-items:center;justify-content:center}
  .about-photo{left:668px;top:795px;width:340px;height:421px;background:linear-gradient(160deg,#5d5d5d 0%,#9c8f84 35%,#ece9e4 60%,#d8cfc2 100%);box-shadow:0 0 0 2px #eee}
  .deco{width:60px;height:60px;background:#fbf3e2;transform:rotate(45deg)}

  /* services */
  .service{width:240px}
  .service .num{font:700 38px "Open Sans",sans-serif;color:var(--gold)}
  .service h3{margin-top:4px;font:600 21px "Open Sans",sans-serif;color:#333}
  .service p{margin-top:10px;font:400 12px/23px "Lato",sans-serif;color:var(--text);text-align:justify}

  /* blog */
  .blog-bg{left:0;top:1620px;width:1200px;height:600px;background:var(--cream)}
  .blog-title{left:0;top:1700px;width:1200px;text-align:center}
  .card{top:1775px;width:318px;height:378px;background:var(--white);border:1px solid #e4e4e4}
  .card .photo{height:183px;width:100%}
  .card .date{position:absolute;left:16px;top:163px;width:111px;height:31px;background:var(--gold);border:2px solid #3a2a00;color:var(--white);font:600 12px "Open Sans",sans-serif;display:flex;align-items:center;justify-content:center}
  .card .body{padding:38px 14px 0}
  .card h4{font:700 13px/21px "Open Sans",sans-serif;color:#222}
  .card p{margin-top:10px;font:400 12px/22px "Lato",sans-serif;color:var(--muted)}
  .card .more{display:inline-block;margin-top:6px;font:600 12px "Open Sans",sans-serif;color:#333;border-bottom:1px solid #333}

  /* contact strip */
  .rule{left:98px;width:1003px;height:2px;background:var(--line)}
  .contact-kicker{left:98px;top:2292px;font:400 22px "Open Sans",sans-serif;color:#333}
  .contact-head{left:98px;top:2326px;font:400 28px "Open Sans",sans-serif;color:#222}
  .contact-btn{left:783px;top:2301px;width:317px;height:52px;background:var(--white);box-shadow:0 4px 14px rgba(0,0,0,.18);display:flex;align-items:center;justify-content:space-between;padding:0 26px 0 35px;font:400 16px "Open Sans",sans-serif;color:#333}

  /* footer */
  .footer-shape{left:0;top:2370px}
  .footer-links{display:flex;flex-direction:column;gap:8px;font:700 14px/18px "Open Sans",sans-serif;color:var(--white)}
  .social{top:2438px;width:48px;height:48px;border:2px solid var(--gold);border-radius:50%}
  .copyright{left:0;top:2655px;width:1200px;text-align:center;font:400 11px "Open Sans",sans-serif;color:var(--white)}
</style>
</head>
<body>

<header>
  <div class="topbar abs">
    <a class="cta abs" href="#">CLICK HERE</a>
    <span class="cta-note abs">to get more info</span>
    <span class="phone abs">
      <svg width="15" height="15" viewBox="0 0 24 24" aria-hidden="true"><path fill="#fff" d="M6.6 10.8a15.1 15.1 0 0 0 6.6 6.6l2.2-2.2c.3-.3.7-.4 1-.2 1.1.4 2.3.6 3.6.6.6 0 1 .4 1 1V20c0 .6-.4 1-1 1A17 17 0 0 1 3 4c0-.6.4-1 1-1h3.5c.6 0 1 .4 1 1 0 1.3.2 2.5.6 3.6.1.3 0 .7-.2 1z"/></svg>
      (55) 0100.4477
    </span>
    <a class="login abs" href="#">
      <svg width="14" height="14" viewBox="0 0 24 24" aria-hidden="true"><path fill="#fff" d="M10 17l5-5-5-5v3H2v4h8zM13 3h7v18h-7v-2h5V5h-5z"/></svg>
      LOG IN
    </a>
  </div>

  <nav class="nav abs">
    <div class="brand abs"><span class="mark"></span>condara</div>
    <div class="menu abs">
      <a href="#">Home</a><a href="#">About</a><a href="#">Services</a><a href="#">Careers</a><a href="#">Contact</a>
      <svg width="15" height="15" viewBox="0 0 24 24" aria-label="Search"><circle cx="10" cy="10" r="7" fill="none" stroke="#222" stroke-width="3"/><path d="M15 15l7 7" stroke="#222" stroke-width="3"/></svg>
    </div>
  </nav>
</header>

<section class="hero abs" role="img" aria-label="Happy family of four standing in front of their apartment building">
  <h1 class="hero-title abs">Condara</h1>
  <p class="hero-text abs">Lorem ipsum dolor sit amet, consectetur adipiscing elit, sed do eiusmod tempor incidim</p>
  <a class="btn-gold abs" href="#">LEARN MORE</a>
  <div class="dots abs"><span></span><span></span><span class="on"></span><span></span></div>
</section>

<section class="about">
  <h2 class="section-title about-title abs">ABOUT<br><span class="accent">CONDARA</span></h2>
  <div class="about-copy abs">
    <p>Sed ut perspiciatis unde omnis iste natus error sit voluptatem accusan tium doloremque laudantium, totam rem aperiam, eaque ipsa quae ab illo inventore veritatis et quasi architecto beatae vitae dicta sunt expli cabo. Nemo enim ipsam voluptatem quia volup tas sit aspernatur aut odit aut fugit dicta sunt explicabo.</p>
    <p>Eaque ipsa quae ab illo inventore veritatis et quasi architecto beatae vitae dicta sunt explicabo. Nemo enim ipsam voluptatem quia volup tas sit aspernatur aut odit aut fugit beatae vitae dicta.</p>
  </div>
  <a class="btn-outline abs" href="#">MORE ABOUT US</a>
  <div class="about-photo abs" role="img" aria-label="Hands reviewing financial reports with a pen beside a laptop"></div>
  <div class="deco abs" style="left:48px;top:1188px"></div>
  <div class="deco abs" style="left:1105px;top:1570px;width:44px;height:44px"></div>
</section>

<section class="services">
  <article class="service abs" style="left:176px;top:1340px">
    <div class="num">01</div>
    <h3>DEBT COLLECTION</h3>
    <p>Sed ut perspiciatis unde omnis iste natus error sit voluptatem accusantium dolo remque laudantium, totam rem aperiam, eaque ipsa quae ab illo inventore veritatis et quasi architecto beatae vitae quia volup.</p>
  </article>
  <article class="service abs" style="left:484px;top:1338px">
    <div class="num">02</div>
    <h3>INVOICE CHECKING</h3>
    <p>Sed ut perspiciatis unde omnis iste natus error sit voluptatem accusantium dolo remque laudantium, totam rem aperiam, eaque ipsa quae ab illo inventore veritatis et quasi architecto beatae vitae quia volup.</p>
  </article>
  <article class="service abs" style="left:793px;top:1338px">
    <div class="num">03</div>
    <h3>INSOLVENCY SERVICES</h3>
    <p>Sed ut perspiciatis unde omnis iste natus error sit voluptatem accusantium dolo remque laudantium, totam rem aperiam, eaque ipsa quae ab illo inventore veritatis et quasi architecto beatae vitae quia volup.</p>
  </article>
</section>

<section class="blog">
  <div class="blog-bg abs"></div>
  <h2 class="section-title blog-title abs">OUR <span class="accent">BLOG</span></h2>

  <article class="card abs" style="left:98px">
    <div class="photo" role="img" aria-label="Hand writing figures next to a calculator" style="background:linear-gradient(135deg,#c98a3e,#f0d9a8 55%,#8b6a4a)"></div>
    <span class="date">10 July, 2018</span>
    <div class="body">
      <h4>Nam a lectus sed lectus aliquam egestas sit amet vitae eratec vitae rutrum lectus.</h4>
      <p>Curabitur aliquet orci nunc, id pellentesque enim facili sisa. Vestibulum mollis vitae dictum eros.</p>
      <a class="more" href="#">Read More</a>
    </div>
  </article>

  <article class="card abs" style="left:440px">
    <div class="photo" role="img" aria-label="Resident talking with a collector at an apartment door" style="background:linear-gradient(90deg,#c9926a,#e8d3bd 45%,#3a3a3a 70%,#b98a5e)"></div>
    <span class="date">10 July, 2018</span>
    <div class="body">
      <h4>Nam a lectus sed lectus aliquam egestas sit amet vitae eratec vitae rutrum lectus.</h4>
      <p>Curabitur aliquet orci nunc, id pellentesque enim facili sisa. Vestibulum mollis vitae dictum eros.</p>
      <a class="more" href="#">Read More</a>
    </div>
  </article>

  <article class="card abs" style="left:783px">
    <div class="photo" role="img" aria-label="Hands with a bank card over a calculator" style="background:linear-gradient(135deg,#e8ecef,#b9c3cc 50%,#7d8a96)"></div>
    <span class="date">10 July, 2018</span>
    <div class="body">
      <h4>Nam a lectus sed lectus aliquam egestas sit amet vitae eratec vitae rutrum lectus.</h4>
      <p>Curabitur aliquet orci nunc, id pellentesque enim facili sisa. Vestibulum mollis vitae dictum eros.</p>
      <a class="more" href="#">Read More</a>
    </div>
  </article>
</section>

<section class="contact">
  <div class="rule abs" style="top:2243px"></div>
  <p class="contact-kicker abs">Lorem Ipsum Is Simple</p>
  <p class="contact-head abs">Do You Need Help Contact Us Now</p>
  <a class="contact-btn abs" href="#">To Contact Email Us
    <svg width="22" height="12" viewBox="0 0 22 12" aria-hidden="true"><path d="M0 6h19M14 1l6 5-6 5" fill="none" stroke="#e9a81f" stroke-width="2"/></svg>
  </a>
  <div class="rule abs" style="top:2415px"></div>
</section>

<footer>
  <svg class="footer-shape abs" width="1200" height="317" viewBox="0 2370 1200 317" aria-hidden="true">
    <defs>
      <linearGradient id="footerGold" x1="0" y1="0" x2="0" y2="1">
        <stop offset="0" stop-color="#f2c23c"/>
        <stop offset="1" stop-color="#e6a21c"/>
      </linearGradient>
    </defs>
    <path d="M195 2687 C250 2560 280 2420 340 2392 C370 2378 410 2376 440 2384 L1110 2610 C1150 2624 1185 2640 1200 2660 L1200 2687 Z" fill="url(#footerGold)"/>
  </svg>
  <nav class="footer-links abs" style="left:337px;top:2475px">
    <a href="#">Home</a><a href="#">About Us</a><a href="#">Services</a><a href="#">Careers</a><a href="#">Contact Us</a>
  </nav>
  <nav class="footer-links abs" style="left:500px;top:2493px">
    <a href="#">Terms &amp; Condition</a><a href="#">Private Policy</a><a href="#">Support</a><a href="#">Newsletter</a>
  </nav>
  <a class="social abs" href="#" aria-label="Social profile 1" style="left:925px"></a>
  <a class="social abs" href="#" aria-label="Social profile 2" style="left:990px"></a>
  <a class="social abs" href="#" aria-label="Social profile 3" style="left:1054px"></a>
  <p class="copyright abs">Copyright © 2018. All Rights Reserved</p>
</footer>

</body>
</html>
```